Commercial Cleaning Company Website Design

We are working with Harbor Tidy Team. They are a commercial cleaning company that needs a new website design.

Some sites to use for inspiration:

https://www.plenvask.com
https://gleam-panecare.com
https://tidwellhelpers.net
https://quietnesthouse.com
https://www.thedustingbureau.com
https://www.pennytidy.com

Thank you for taking the time to consider designing a website for us. We are web developers based in Stockton and Los Angeles, CA, USA. Most of our projects go through the same process. Understanding this process may help you win a project with us. We custom-code all of our websites in-house. We don’t have any requirements as to what tools you use for your design, but we prefer Figma files. For any design that we label as four-stars, we send it to the client for review. The client picks the final design they want us to use. Once we complete this process, we will continue to show additional clients all the four-star sites and purchase them later. Your designs will have multiple chances to sell. For better chances of success, we ask that you follow these guidelines.

IMAGES:
If you use any images or icons in the design, we ask that you have a link to the asset so we can purchase the image/icon. Most of the designs we submit do not have the customer’s images on them unless they have some great images. Be creative; show us the feeling you are trying to portray with your image choices. Use any royalty-free site you choose. We subscribe to Adobe and mainly use their images, but we can purchase images outside of Adobe.

PLEASE NOTE: we will not submit designs to clients with watermarks on the images.

FONTS:
We ask that you identify the fonts used in the design. This can be done in a message if you want. We typically use Google Fonts and Adobe Fonts.

CONTENT:
We're always open to different content and ideas. We often submit designs with stock images so the client can see our vision. We typically take pictures after the website launch to use their images with our vision. Lorem Ipsum is fine for paragraphs, but we ask that you write the headers in correct English. We want to be able to show the vision and identify the sections of the website.

INSPIRATION:
We typically add a couple of links in the brief of websites we like to help you get started in your design.

REVISIONS:
We do not often ask for revisions of the designs unless we see something in the design that may not appeal to the client. If there are slight changes that we want to make, we do that in the development process.

FEEDBACK:
We rarely give feedback on designs during the design process. We are working on many website projects and do not have the time to provide feedback. We usually respond if your request is well thought out and asks specific questions, but a note asking “feedback, please” usually goes unanswered.

```html
<!DOCTYPE html>
<html lang="en">
<head>
<meta charset="utf-8">
<title>Harbor Tidy Team – Commercial Cleaning</title>
<link href="https://fonts.googleapis.com/css2?family=Kanit:wght@400;500;600&family=Inter:wght@400;500;600;700&display=swap" rel="stylesheet">
<style>
:root{
  --red:#e3131b;
  --red-deep:#c90f17;
  --blue:#1636b4;
  --blue-deep:#0f2a94;
  --ink:#1b1c22;
  --text:#55585f;
  --dark:#17181e;
  --white:#ffffff;
}
*{box-sizing:border-box;margin:0;padding:0}
html,body{width:1200px;height:5051px;overflow:hidden;background:#fff}
body{font-family:"Inter",Arial,sans-serif;color:var(--ink)}
.canvas{position:relative;width:1200px;height:5051px;overflow:hidden;background:#fff}
.abs{position:absolute}
.head-font{font-family:"Kanit",Arial,sans-serif}
.pill{position:absolute;display:flex;align-items:center;justify-content:center;border-radius:30px;color:#fff;font-weight:600;font-size:14px;white-space:nowrap}
.pill.red{background:var(--red)}
.pill.blue{background:var(--blue)}
.eyebrow{position:absolute;left:0;width:1200px;text-align:center;font-size:15px;font-weight:600;letter-spacing:3px;color:var(--red)}
.section-title{position:absolute;left:0;width:1200px;text-align:center;font-family:"Kanit",Arial,sans-serif;font-weight:500;font-size:40px;color:var(--blue);line-height:1}
.on-color{color:#fff}

/* header */
.logo{position:absolute;display:flex;align-items:center;gap:12px}
.logo-dot{width:30px;height:30px;border-radius:50%;background:var(--red)}
.logo-name{font-family:"Kanit",Arial,sans-serif;font-weight:500;font-size:22px;letter-spacing:4px;color:var(--blue)}
.top-phone{position:absolute;left:555px;top:30px;font-size:14px;font-weight:600;color:var(--red);display:flex;align-items:center;gap:8px}
.nav{position:absolute;top:77px;left:462px;display:flex;gap:0;font-size:14px;color:#555}
.nav a{position:absolute;white-space:nowrap;text-decoration:none;color:#555}
.nav a.active{color:var(--blue);font-weight:700;border-bottom:2px solid var(--blue);padding-bottom:2px}

/* hero */
.hero-photo{position:absolute;left:0;top:115px;width:1200px;height:645px;background:linear-gradient(120deg,#2a2b30 0%,#4a4b50 45%,#34353a 70%,#1f2024 100%)}
.hero-shade{position:absolute;left:0;top:115px;width:1200px;height:645px;background:linear-gradient(90deg,rgba(0,0,0,.55),rgba(0,0,0,.15))}
.hero-h1{position:absolute;left:110px;top:262px;color:#fff;font-family:"Kanit",Arial,sans-serif;font-weight:500;line-height:1.05}
.hero-h1 .big{font-size:56px;display:block}
.hero-h1 .mid{font-size:41px;display:block;margin-top:6px;line-height:1.25}
.hero-p{position:absolute;left:110px;top:440px;width:470px;color:#fff;font-size:17px;line-height:1.65}

.quote-box{position:absolute;left:674px;top:290px;width:360px;height:468px;background:var(--red);border-radius:20px;box-shadow:0 20px 40px rgba(0,0,0,.25)}
.quote-title{position:absolute;top:26px;left:0;width:100%;text-align:center;color:#fff;font-family:"Kanit",Arial,sans-serif;font-weight:500;font-size:25px}
.field{position:absolute;left:33px;width:295px;height:42px;background:#fff;border-radius:6px;display:flex;align-items:center;padding-left:16px;gap:12px;font-size:11px;color:#555}
.field.tall{height:122px;align-items:flex-start;padding-top:14px}
.send{position:absolute;left:33px;top:390px;width:295px;height:42px;background:var(--blue);border-radius:6px;color:#fff;font-size:12px;display:flex;align-items:center;justify-content:center;font-weight:500}

/* about */
.about-lead{position:absolute;left:200px;width:800px;top:920px;text-align:center;font-size:16px;font-weight:600;line-height:1.85;color:#222}
.about-body{position:absolute;left:190px;width:820px;top:1010px;text-align:center;font-size:16px;line-height:1.9;color:#6a6c72}
.feature{position:absolute;top:1201px;width:186px;height:186px;background:#fff;border-radius:16px;box-shadow:0 10px 30px rgba(22,54,180,.12);text-align:center}
.feature .ic{width:66px;height:66px;border-radius:50%;margin:32px auto 0;display:flex;align-items:center;justify-content:center}
.feature p{margin-top:16px;font-size:15px;font-weight:500;line-height:1.45;color:#444}

/* services */
.svc{position:absolute;top:1803px;width:231px;height:357px;background:#fff;border-radius:14px;overflow:hidden;box-shadow:0 10px 24px rgba(0,0,0,.2)}
.svc .img{position:absolute;left:0;top:0;width:231px;height:192px}
.svc .ic{position:absolute;left:84px;top:158px;width:64px;height:64px;border-radius:50%;border:4px solid #fff;display:flex;align-items:center;justify-content:center}
.svc h3{position:absolute;top:240px;left:0;width:100%;text-align:center;font-family:"Kanit",Arial,sans-serif;font-weight:500;font-size:17px}
.svc p{position:absolute;top:270px;left:18px;width:195px;text-align:center;font-size:13px;line-height:1.8;color:#666}

/* why */
.why{position:absolute;top:2515px;width:225px;height:282px;border-radius:14px;background:rgba(190,10,18,.55);box-shadow:0 10px 24px rgba(0,0,0,.18);text-align:center;color:#fff}
.why.outlined{border:1.5px solid #fff}
.why .ic{width:66px;height:66px;border-radius:50%;background:#fff;margin:40px auto 0;display:flex;align-items:center;justify-content:center}
.why h3{margin-top:26px;font-family:"Kanit",Arial,sans-serif;font-weight:500;font-size:15px}
.why p{margin:10px auto 0;width:190px;font-size:13px;line-height:1.8}

/* testimonials */
.testi{position:absolute;top:3189px;width:463px;height:368px;background:#fff;border-radius:20px;box-shadow:0 10px 34px rgba(0,0,0,.08);text-align:center}
.testi .stars{margin-top:40px;display:flex;justify-content:center;gap:2px}
.testi p{margin:10px auto 0;width:380px;font-size:14px;line-height:1.85;color:#666}
.testi .name{margin-top:18px;font-weight:600;font-size:14px;color:var(--blue)}

/* projects */
.proj{position:absolute;border-radius:26px}

/* cta */
.cta-h{position:absolute;left:108px;top:4463px;color:#fff;font-family:"Kanit",Arial,sans-serif;font-weight:500;font-size:38px;line-height:1.25}
.cta-p{position:absolute;left:651px;top:4335px;width:450px;color:#fff;font-size:16px;line-height:1.85}
.contact-row{position:absolute;left:651px;display:flex;align-items:center;gap:22px;color:#fff}
.contact-row .dot{width:48px;height:48px;border-radius:50%;background:var(--red);display:flex;align-items:center;justify-content:center}
.contact-row small{display:block;font-size:14px}
.contact-row strong{display:block;font-size:23px;font-weight:700;margin-top:4px}

/* footer */
.foot-h{position:absolute;top:4718px;color:#fff;font-family:"Kanit",Arial,sans-serif;font-weight:500;font-size:23px}
.foot-list{position:absolute;top:4768px;list-style:none;color:#fff;font-size:14px}
.foot-list li{height:35px;display:flex;align-items:flex-start;gap:22px}
.foot-list li i{width:11px;height:11px;border-radius:50%;background:var(--red);display:inline-block;margin-top:3px;flex:none}
.social{position:absolute;top:4724px;width:40px;height:40px;border-radius:50%;background:var(--red)}
.rule{position:absolute;left:108px;top:4990px;width:984px;height:1px;background:rgba(255,255,255,.25)}
.copy{position:absolute;top:5016px;left:0;width:1200px;text-align:center;color:#fff;font-size:12px}
</style>
</head>
<body>
<div class="canvas">

  <!-- background bands -->
  <svg class="abs" style="left:0;top:0" width="1200" height="5051" viewBox="0 0 1200 5051">
    <polygon points="0,1548 1200,1625 1200,1700 0,1700" fill="#e3131b"/>
    <polygon points="0,1672 1200,1548 1200,2390 0,2420" fill="#1636b4"/>
    <polygon points="0,2380 1200,2340 1200,2830 0,3092" fill="#e3131b"/>
    <polygon points="0,4395 1200,4273 1200,4694 0,4694" fill="#1636b4"/>
    <polygon points="0,4694 1200,4580 1200,5051 0,5051" fill="#17181e"/>
  </svg>

  <!-- header -->
  <div class="logo" style="left:108px;top:40px">
    <span class="logo-dot"></span><span class="logo-name">HARBOR TIDY TEAM</span>
  </div>
  <div class="top-phone">
    <svg width="13" height="13" viewBox="0 0 24 24"><path fill="#e3131b" d="M6.6 10.8a15.1 15.1 0 0 0 6.6 6.6l2.2-2.2c.3-.3.7-.4 1-.2 1.1.4 2.3.6 3.6.6.6 0 1 .4 1 1V20c0 .6-.4 1-1 1A17 17 0 0 1 3 4c0-.6.4-1 1-1h3.5c.6 0 1 .4 1 1 0 1.3.2 2.5.6 3.6.1.3 0 .7-.2 1z"/></svg>
    Call Us: +1 555 010 (2040)
  </div>
  <div class="pill red" style="left:800px;top:21px;width:116px;height:37px">Book Now</div>
  <div class="pill blue" style="left:933px;top:21px;width:153px;height:37px">Request a Quote</div>
  <nav class="nav">
    <a class="active" style="left:0">Home</a>
    <a style="left:83px">About Us</a>
    <a style="left:188px">Services</a>
    <a style="left:289px">Projects</a>
    <a style="left:387px">Why Choose Us?</a>
    <a style="left:546px">Contact Us</a>
  </nav>

  <!-- hero -->
  <div class="hero-photo" role="img" aria-label="Office team cleaning a workspace in black and white"></div>
  <div class="hero-shade"></div>
  <svg class="abs" style="left:0;top:620px" width="1200" height="141" viewBox="0 0 1200 141"><polygon points="0,141 1200,17 1200,141" fill="#fff"/></svg>
  <h1 class="hero-h1"><span class="big">PROFESSIONAL</span><span class="mid">COMMERCIAL CLEANING<br>YOU CAN RELY ON</span></h1>
  <p class="hero-p">Keeping your business spotless, safe, and ready for success — every single day.</p>
  <div class="pill red" style="left:110px;top:520px;width:175px;height:42px">Get a Free Quote</div>
  <div class="pill blue" style="left:300px;top:520px;width:224px;height:42px">Call: +1 555 010 (2040)</div>

  <form class="quote-box">
    <div class="quote-title">REQUEST A QUOTE</div>
    <div class="field" style="top:76px"><svg width="11" height="11" viewBox="0 0 24 24"><circle cx="12" cy="7" r="5" fill="#555"/><path d="M3 23c0-5 4-9 9-9s9 4 9 9z" fill="#555"/></svg>Full Name</div>
    <div class="field" style="top:134px"><svg width="12" height="10" viewBox="0 0 24 18"><rect width="24" height="18" rx="2" fill="#555"/><path d="M1 2l11 8 11-8" stroke="#fff" stroke-width="2" fill="none"/></svg>Email Address</div>
    <div class="field" style="top:193px"><svg width="11" height="11" viewBox="0 0 24 24"><path fill="#555" d="M6.6 10.8a15.1 15.1 0 0 0 6.6 6.6l2.2-2.2c.3-.3.7-.4 1-.2 1.1.4 2.3.6 3.6.6.6 0 1 .4 1 1V20c0 .6-.4 1-1 1A17 17 0 0 1 3 4c0-.6.4-1 1-1h3.5c.6 0 1 .4 1 1 0 1.3.2 2.5.6 3.6.1.3 0 .7-.2 1z"/></svg>Phone Number</div>
    <div class="field tall" style="top:251px"><svg width="12" height="11" viewBox="0 0 24 22"><path d="M2 2h20v14H8l-6 5z" fill="#555"/></svg>Comments</div>
    <div class="send">Send Message</div>
  </form>

  <!-- about -->
  <div class="eyebrow" style="top:828px">INTRODUCTION</div>
  <h2 class="section-title" style="top:858px">ABOUT HARBOR TIDY TEAM</h2>
  <p class="about-lead">For over 15+ years, Harbor Tidy Team has been the trusted partner for property managers, contractors, and business owners who demand a higher standard of cleanliness.</p>
  <p class="about-body">Sed ut perspiciatis unde omnis iste natus error sit voluptatem accusantium doloremque laudantium, totam rem aperiam, eaque ipsa quae ab illo inventore veritatis et quasi architecto beatae vitae dicta sunt explicabo. Nemo enim ipsam voluptatem quia voluptas sit aspernatur aut odit aut fugit, sed quia consequuntur magni dolores eos qui ratione voluptatem sequi nesciunt. Neque porro quisquam est qui dolorem ipsum quia dolor sit amet, consectetur, adipisci velit</p>

  <div class="feature" style="left:292px">
    <div class="ic" style="background:var(--red)"><svg width="34" height="34" viewBox="0 0 24 24"><circle cx="12" cy="12" r="9" fill="#fff"/><path d="M8 12l3 3 5-6" stroke="#e3131b" stroke-width="2.2" fill="none"/></svg></div>
    <p>Fully Licensed &amp;<br>Insured</p>
  </div>
  <div class="feature" style="left:506px">
    <div class="ic" style="background:var(--blue)"><svg width="34" height="34" viewBox="0 0 24 24"><circle cx="12" cy="12" r="9" fill="none" stroke="#fff" stroke-width="2"/><path d="M7 15c2-6 6-8 10-8-1 5-4 9-10 8z" fill="#fff"/></svg></div>
    <p>Green-Certified<br>Cleaning</p>
  </div>
  <div class="feature" style="left:720px">
    <div class="ic" style="background:var(--red)"><svg width="34" height="34" viewBox="0 0 24 24"><path d="M12 2a7 7 0 0 0-7 7c0 5 7 13 7 13s7-8 7-13a7 7 0 0 0-7-7z" fill="#fff"/><circle cx="12" cy="9" r="2.6" fill="#e3131b"/></svg></div>
    <p>Locally Owned &amp;<br>Operated</p>
  </div>
  <div class="pill blue" style="left:520px;top:1425px;width:158px;height:42px">Explore More</div>

  <!-- services -->
  <div class="eyebrow on-color" style="top:1700px">COMPLETE COMMERCIAL CLEANING SOLUTIONS</div>
  <h2 class="section-title on-color" style="top:1728px">OUR CORE SERVICES</h2>

  <div class="svc" style="left:118px">
    <div class="img" role="img" aria-label="Janitor cleaning an office lounge floor" style="background:linear-gradient(135deg,#8a97a8,#3c4654)"></div>
    <div class="ic" style="background:var(--blue)"><svg width="28" height="28" viewBox="0 0 24 24"><rect x="4" y="9" width="16" height="10" rx="2" fill="#fff"/><rect x="9" y="4" width="6" height="5" fill="#fff"/></svg></div>
    <h3 style="color:var(--blue)">JANITORIAL CLEANING</h3>
    <p>Reliable daily or nightly service for offices, schools, and public buildings..</p>
  </div>
  <div class="svc" style="left:367px">
    <div class="img" role="img" aria-label="Mopping a glossy office floor" style="background:linear-gradient(135deg,#c9d2d9,#6c7780)"></div>
    <div class="ic" style="background:var(--red)"><svg width="28" height="28" viewBox="0 0 24 24"><rect x="11" y="2" width="2" height="12" fill="#fff"/><path d="M6 14h12l1 7H5z" fill="#fff"/></svg></div>
    <h3 style="color:var(--red)">FLOOR CARE</h3>
    <p>Reliable daily or nightly service for offices, schools, and public buildings..</p>
  </div>
  <div class="svc" style="left:616px">
    <div class="img" role="img" aria-label="Worker in protective suit sanitizing a room" style="background:linear-gradient(135deg,#b7c6d6,#546173)"></div>
    <div class="ic" style="background:var(--blue)"><svg width="28" height="28" viewBox="0 0 24 24"><rect x="6" y="8" width="9" height="13" rx="2" fill="#fff"/><rect x="8" y="4" width="6" height="4" fill="#fff"/><circle cx="19" cy="6" r="1.3" fill="#fff"/><circle cx="20" cy="10" r="1.3" fill="#fff"/></svg></div>
    <h3 style="color:var(--blue)">SANITIZATION</h3>
    <p>Reliable daily or nightly service for offices, schools, and public buildings..</p>
  </div>
  <div class="svc" style="left:865px">
    <div class="img" role="img" aria-label="Cleaner washing tall office windows" style="background:linear-gradient(135deg,#dfe6ea,#8fa0ac)"></div>
    <div class="ic" style="background:var(--blue)"><svg width="28" height="28" viewBox="0 0 24 24"><circle cx="9" cy="14" r="5" fill="#fff"/><circle cx="16" cy="8" r="3.5" fill="#fff"/><circle cx="18" cy="16" r="2.5" fill="#fff"/></svg></div>
    <h3 style="color:var(--blue)">GLASS CLEANING</h3>
    <p>Reliable daily or nightly service for offices, schools, and public buildings..</p>
  </div>
  <div class="pill red" style="left:508px;top:2198px;width:184px;height:42px">View All Services</div>

  <!-- why choose us -->
  <div class="eyebrow on-color" style="top:2410px">EXPERIENCE. RELIABILITY. RESULTS YOU CAN SEE.</div>
  <h2 class="section-title on-color" style="top:2440px">WHY CHOOSE US?</h2>

  <div class="why" style="left:116px">
    <div class="ic"><svg width="32" height="32" viewBox="0 0 24 24"><circle cx="12" cy="8" r="3.5" fill="#e3131b"/><circle cx="5" cy="10" r="2.5" fill="#e3131b"/><circle cx="19" cy="10" r="2.5" fill="#e3131b"/><path d="M6 20c0-4 3-7 6-7s6 3 6 7z" fill="#e3131b"/></svg></div>
    <h3>TRAINED &amp; VETTED STAFF</h3>
    <p>All our cleaners are background-checked, fully trained, and dedicated to maintaining</p>
  </div>
  <div class="why outlined" style="left:366px">
    <div class="ic"><svg width="40" height="40" viewBox="0 0 24 24"><circle cx="12" cy="12" r="11" fill="#1636b4"/><path d="M7 15c2-6 6-8 10-8-1 5-4 9-10 8z" fill="#fff"/></svg></div>
    <h3>ECO-FRIENDLY PRODUCTS</h3>
    <p>All our cleaners are background-checked, fully trained, and dedicated to maintaining</p>
  </div>
  <div class="why" style="left:615px">
    <div class="ic"><svg width="32" height="32" viewBox="0 0 24 24"><rect x="3" y="5" width="18" height="16" rx="2" fill="#e3131b"/><rect x="5" y="10" width="14" height="9" fill="#fff"/><rect x="7" y="3" width="2" height="4" fill="#e3131b"/><rect x="15" y="3" width="2" height="4" fill="#e3131b"/></svg></div>
    <h3>FLEXIBLE SCHEDULING</h3>
    <p>All our cleaners are background-checked, fully trained, and dedicated to maintaining</p>
  </div>
  <div class="why" style="left:864px">
    <div class="ic"><svg width="32" height="32" viewBox="0 0 24 24"><circle cx="12" cy="13" r="8" fill="none" stroke="#e3131b" stroke-width="2.4"/><path d="M12 9v4l3 2" stroke="#e3131b" stroke-width="2" fill="none"/><rect x="10" y="2" width="4" height="2" fill="#e3131b"/></svg></div>
    <h3>FAST RESPONSIVE</h3>
    <p>All our cleaners are background-checked, fully trained, and dedicated to maintaining</p>
  </div>
  <div class="pill blue" style="left:508px;top:2834px;width:184px;height:42px">Request a Quote</div>

  <!-- testimonials -->
  <div class="eyebrow" style="top:3083px">TESTIMONIALS</div>
  <h2 class="section-title" style="top:3110px">WHAT OUR CLIENTS SAY</h2>

  <svg class="abs" style="left:108px;top:3352px" width="46" height="46" viewBox="0 0 46 46"><circle cx="23" cy="23" r="21" fill="#fff" stroke="#e3131b" stroke-width="1.5"/><path d="M24 17l-6 6 6 6M30 17l-6 6 6 6" stroke="#e3131b" stroke-width="1.8" fill="none"/></svg>
  <svg class="abs" style="left:1178px;top:3352px" width="22" height="46" viewBox="0 0 22 46"><circle cx="23" cy="23" r="21" fill="#f8c9cb"/></svg>

  <div class="testi" style="left:182px">
    <div class="stars"><svg width="70" height="14" viewBox="0 0 70 14"><g fill="#e3131b"><path id="st" d="M7 0l2 4.5 5 .5-3.8 3.3 1.1 5L7 10.8 2.7 13.3l1.1-5L0 5l5-.5z"/><use href="#st" x="14"/><use href="#st" x="28"/><use href="#st" x="42"/></g><path d="M63 0l2 4.5 5 .5-3.8 3.3 1.1 5L63 10.8l-4.3 2.5 1.1-5L56 5l5-.5z" fill="none" stroke="#e3131b"/></svg></div>
    <p>Sed ut perspiciatis unde omnis iste natus error sit voluptatem accusantium doloremque laudantium, totam rem aperiam, eaque ipsa quae ab illo inventore veritatis et quasi architecto beatae vitae dicta sunt explicabo.<br><br>Nemo enim ipsam voluptatem quia voluptas sit aspernatur aut odit aut fugit, sed quia consequuntur magni</p>
    <div class="name">Daniel Marsh</div>
  </div>
  <div class="testi" style="left:688px">
    <div class="stars"><svg width="70" height="14" viewBox="0 0 70 14"><g fill="#e3131b"><use href="#st"/><use href="#st" x="14"/><use href="#st" x="28"/><use href="#st" x="42"/></g><path d="M63 0l2 4.5 5 .5-3.8 3.3 1.1 5L63 10.8l-4.3 2.5 1.1-5L56 5l5-.5z" fill="none" stroke="#e3131b"/></svg></div>
    <p>Sed ut perspiciatis unde omnis iste natus error sit voluptatem accusantium doloremque laudantium, totam rem aperiam, eaque ipsa quae ab illo inventore veritatis et quasi architecto beatae vitae dicta sunt explicabo.<br><br>Nemo enim ipsam voluptatem quia voluptas sit aspernatur aut odit aut fugit, sed quia consequuntur magni</p>
    <div class="name">Daniel Marsh</div>
  </div>

  <!-- projects -->
  <div class="eyebrow" style="top:3620px">FEATURED PROJECTS</div>
  <h2 class="section-title" style="top:3649px">SEE THE DIFFERENCE WE MAKE</h2>
  <div class="proj" role="img" aria-label="Cleaner wiping a white countertop" style="left:-30px;top:3744px;width:270px;height:378px;background:linear-gradient(135deg,#e9ece4,#b9c0a7)"></div>
  <div class="proj" role="img" aria-label="Cleaner mopping a wooden office floor" style="left:274px;top:3730px;width:650px;height:392px;background:linear-gradient(135deg,#d8dce4,#7c6a58);box-shadow:0 24px 30px -14px rgba(0,0,0,.35)"></div>
  <div class="proj" role="img" aria-label="Cleaner washing a window with yellow gloves" style="left:958px;top:3744px;width:270px;height:378px;background:linear-gradient(135deg,#cfe0bf,#e9eef0)"></div>
  <div class="pill blue" style="left:504px;top:4163px;width:192px;height:42px">See More Projects</div>

  <!-- cta -->
  <p class="cta-p">Get a customized cleaning plan built around your business needs. No contracts. No hassle. Just spotless results.</p>
  <div class="abs" style="left:108px;top:4428px;color:#fff;font-size:15px;font-weight:600;letter-spacing:3px">REQUEST A FREE QUOTE</div>
  <h2 class="cta-h">READY FOR A CLEANER,<br>HEALTHIER WORKPLACE?</h2>
  <div class="contact-row" style="top:4455px">
    <span class="dot"><svg width="18" height="18" viewBox="0 0 24 24"><path fill="#fff" d="M6.6 10.8a15.1 15.1 0 0 0 6.6 6.6l2.2-2.2c.3-.3.7-.4 1-.2 1.1.4 2.3.6 3.6.6.6 0 1 .4 1 1V20c0 .6-.4 1-1 1A17 17 0 0 1 3 4c0-.6.4-1 1-1h3.5c.6 0 1 .4 1 1 0 1.3.2 2.5.6 3.6.1.3 0 .7-.2 1z"/></svg></span>
    <div><small>Call Us:</small><strong>+1 555 010 (2040)</strong></div>
  </div>
  <div class="contact-row" style="top:4545px">
    <span class="dot"><svg width="18" height="14" viewBox="0 0 24 18"><rect width="24" height="18" rx="2" fill="#fff"/><path d="M1 2l11 8 11-8" stroke="#e3131b" stroke-width="2" fill="none"/></svg></span>
    <div><small>Email Us:</small><strong>info@harbortidyteam.com</strong></div>
  </div>

  <!-- footer -->
  <div class="logo" style="left:108px;top:4762px">
    <span class="logo-dot"></span><span class="logo-name" style="color:#fff">HARBOR TIDY TEAM</span>
  </div>
  <div class="foot-h" style="left:438px">QUICK LINKS</div>
  <ul class="foot-list" style="left:438px">
    <li><i></i>Home</li><li><i></i>About Us</li><li><i></i>Services</li><li><i></i>Projects</li><li><i></i>Testimonials</li><li><i></i>Contact Us</li>
  </ul>
  <div class="foot-h" style="left:666px">CONTACT INFO</div>
  <ul class="foot-list" style="left:666px">
    <li><i></i>Harbor Tidy Team</li><li><i></i>1234 Harbor Blvd, Suite 200,</li><li><i></i>Bayview, WA 98000</li><li><i></i></li><li><i></i>+1 555 010 (2040)</li><li><i></i>info@harbortidyteam.com</li>
  </ul>
  <span class="social" style="left:956px"></span>
  <span class="social" style="left:1002px"></span>
  <span class="social" style="left:1048px"></span>
  <div class="rule"></div>
  <div class="copy">(C) Copyright 2025 | All Rights Reserved</div>
</div>
</body>
</html>
```